KORVAL:advise Business Cards

We need a business card design for KORVAL:advise (Logo Attached), a management consultancy specialized in brand & business building.

Design should be clean, smart and a touch of innnovation without being gimmicky.

The details on the card should be:
Name: Tomas Velduren
Title: Managing Director
Address: 42 Marlowe Pier, Tarn Vessel Tower, Singapore 073926
Tel: +6285927461082
email: tv@korvaladvise.example
website: korvaladvise.example

For further background on corporate identity, please check www.korvaladvise.example
Updates

Dear all,

Many thanks for the submissions so far! I gave feedback to those designs that I prefer at this stage.

Overall I see that my preference goes into the direction that 'less is more' and 'simple is beautiful'

Please create uniqueness and standout by the simplicity and attraction of the overall concept and design.

Many thanks and please shout incase of questions!

Tomas

Industry/Entity Type

Business

```html
<!DOCTYPE html>
<html lang="en">
<head>
<meta charset="utf-8">
<title>KORVAL:advise Business Cards</title>
<link rel="stylesheet" href="https://fonts.googleapis.com/css2?family=Open+Sans:wght@400;600;700&display=swap">
<style>
  :root {
    --orange: #ff6600;
    --orange-pale: #fdd3b8;
    --ink: #4a4a4a;
    --ink-soft: #555555;
    --paper: #ffffff;
    --backdrop: #ecebe8;
  }
  * { box-sizing: border-box; margin: 0; padding: 0; }
  html, body {
    width: 1174px;
    height: 1200px;
    overflow: hidden;
  }
  body {
    background: var(--backdrop);
    font-family: "Open Sans", Arial, sans-serif;
    position: relative;
  }
  .card {
    position: absolute;
    width: 940px;
    height: 536px;
  }
  .card--front {
    left: 28px;
    top: 28px;
    background: var(--paper);
    border: 1px solid #bdbdbd;
  }
  .card--back {
    left: 206px;
    top: 604px;
    background: var(--orange);
  }
  .wordmark {
    position: absolute;
    left: 0;
    right: 0;
    text-align: center;
    font-weight: 600;
    font-size: 76px;
    line-height: 1;
  }
  .card--front .wordmark { top: 146px; color: var(--ink); }
  .card--back .wordmark { top: 196px; color: var(--paper); }

  .identity {
    position: absolute;
    right: 453px;
    top: 308px;
    text-align: right;
    color: var(--ink-soft);
  }
  .identity__name {
    font-weight: 700;
    font-size: 26px;
    color: var(--ink);
    line-height: 36px;
  }
  .identity__title {
    font-size: 21px;
    color: var(--orange);
    line-height: 34px;
  }
  .identity__address {
    font-size: 21px;
    line-height: 34px;
    font-style: normal;
  }
  .divider-marks {
    position: absolute;
    left: 505px;
    top: 316px;
  }
  .divider-marks span {
    display: block;
    width: 18px;
    height: 30px;
    background: var(--orange-pale);
    margin-bottom: 20px;
  }
  .contacts {
    position: absolute;
    left: 536px;
    top: 314px;
    list-style: none;
    font-size: 21px;
    color: var(--ink-soft);
  }
  .contacts li {
    display: flex;
    align-items: center;
    gap: 8px;
    height: 34px;
    margin-bottom: 15px;
  }
  .contacts svg { width: 22px; height: 22px; flex: none; }
  .back-url {
    position: absolute;
    left: 0;
    right: 0;
    top: 376px;
    text-align: center;
    color: var(--paper);
    font-size: 22px;
    letter-spacing: 5px;
  }
</style>
</head>
<body>
  <section class="card card--front">
    <p class="wordmark">KORVAL:advise</p>

    <div class="identity">
      <p class="identity__name">Tomas Velduren</p>
      <p class="identity__title">Managing Director</p>
      <address class="identity__address">42 Marlowe Pier, Tarn<br>Vessel Tower, Singapore 073926</address>
    </div>

    <div class="divider-marks"><span></span><span></span><span></span></div>

    <ul class="contacts">
      <li>
        <svg viewBox="0 0 24 24" aria-hidden="true"><path fill="#ff6600" d="M6.6 10.8a15 15 0 0 0 6.6 6.6l2.2-2.2c.3-.3.7-.4 1-.2 1.1.4 2.3.6 3.6.6.6 0 1 .4 1 1V20c0 .6-.4 1-1 1A17 17 0 0 1 3 4c0-.6.4-1 1-1h3.5c.6 0 1 .4 1 1 0 1.3.2 2.5.6 3.6.1.3 0 .7-.2 1z"/></svg>
        +6285927461082
      </li>
      <li>
        <svg viewBox="0 0 24 24" aria-hidden="true"><circle cx="12" cy="12" r="11" fill="#ff6600"/><rect x="6" y="8" width="12" height="8" fill="#fff"/><path d="M6 8l6 5 6-5" fill="none" stroke="#ff6600" stroke-width="1.4"/></svg>
        tv@korvaladvise.example
      </li>
      <li>
        <svg viewBox="0 0 24 24" aria-hidden="true"><circle cx="12" cy="12" r="10" fill="#ff6600"/><g fill="none" stroke="#fff" stroke-width="1.3"><circle cx="12" cy="12" r="7"/><ellipse cx="12" cy="12" rx="3" ry="7"/><path d="M5 12h14"/></g></svg>
        www.korvaladvise.example
      </li>
    </ul>
  </section>

  <section class="card card--back">
    <p class="wordmark">KORVAL:advise</p>
    <p class="back-url">www.korvaladvise.example</p>
  </section>
</body>
</html>
```